High Tech Real Estate Startup needs a business card

We are developing an innovative real estate marketing product based around advanced search and virtual reality.

We talk to people, we need business cards.

Target Market(s)

The target market is technology professionals and realtors.

Contact Information for Business Card

The information to be included will include

Name
Title
Phone Number
E-mail Address
www.zelquin.com

It should use simple iconography for each one of those fields.

Font styles to use
Other font styles liked:
• Co, Jubilat, Avenir

Colors

Designer to choose colors to be used in the design.

Requirements
Must have
• Clean aesthetic,
• Good use of negative space.
• It should use our company logo, shown in the attached file. It is able to use the negative of that logo (coloured font and white background) and I have attached other acceptable accent colours in a swatch file.
Should not have
• Should not be too busy
• No extraneous text (slogans, tag lines etc)

```html
<!DOCTYPE html>
<html lang="en">
<head>
<meta charset="utf-8">
<title>Zelquin Business Card</title>
<link rel="stylesheet" href="https://fonts.googleapis.com/css2?family=Roboto:wght@400;500&family=Roboto+Condensed:wght@400;500&display=swap">
<style>
  :root {
    --backdrop: #262626;
    --card-teal: #00bbbe;
    --card-shadow: rgba(0, 0, 0, 0.45);
    --ink-white: #ffffff;
    --ink-soft: #e6f7f7;
  }
  * { margin: 0; padding: 0; box-sizing: border-box; }
  html, body {
    width: 1200px;
    height: 960px;
    overflow: hidden;
    background: var(--backdrop);
  }
  .canvas {
    position: relative;
    width: 1200px;
    height: 960px;
  }
  .card {
    position: absolute;
    left: 320px;
    width: 600px;
    height: 342px;
    background: var(--card-teal);
    box-shadow: 0 4px 10px var(--card-shadow);
  }
  .card-front { top: 108px; }
  .card-back { top: 493px; }

  .wordmark {
    position: absolute;
    inset: 0;
    display: flex;
    align-items: center;
    justify-content: center;
    padding-bottom: 10px;
    font-family: "Roboto", sans-serif;
    font-weight: 500;
    font-size: 72px;
    letter-spacing: 3px;
    color: var(--ink-white);
  }

  .contact-block {
    position: absolute;
    left: 0;
    right: 0;
    top: 104px;
    text-align: center;
    color: var(--ink-soft);
    font-family: "Roboto", sans-serif;
  }
  .contact-name {
    font-family: "Roboto Condensed", sans-serif;
    font-weight: 500;
    font-size: 23px;
    line-height: 28px;
    color: var(--ink-white);
  }
  .contact-title {
    font-family: "Roboto Condensed", sans-serif;
    font-weight: 500;
    font-size: 15px;
    line-height: 20px;
  }
  .divider {
    width: 42px;
    height: 1px;
    margin: 7px auto 8px;
    background: var(--ink-soft);
  }
  .contact-line {
    font-size: 14px;
    line-height: 19px;
  }
  .contact-web {
    font-size: 14px;
    line-height: 19px;
    letter-spacing: 1px;
    color: var(--ink-white);
  }
</style>
</head>
<body>
  <main class="canvas">
    <section class="card card-front">
      <div class="wordmark">ZELQUIN</div>
    </section>

    <section class="card card-back">
      <div class="contact-block">
        <p class="contact-name">Adam Verlo</p>
        <p class="contact-title">CEO/Founder</p>
        <div class="divider"></div>
        <p class="contact-line">P. 555 014 2290</p>
        <p class="contact-line">E. adam@zelquin.com</p>
        <div class="divider"></div>
        <p class="contact-web">www.zelquin.com</p>
      </div>
    </section>
  </main>
</body>
</html>
```